Webdesign for a business that converts shops into apps. UPDATE BRIEF

We want a creative/professional design for our new business Vorbo.

Vorbo is a service that can deliver instant apps for quillora shops. So every shop owner can have its own app for selling to there customers.

We are open for your interpretation of the design. We think it could be intersting doing an onepage design for this. But thats not set in stones offcourse.

We need several section:
top section
some facts abt the service and maybe our company
price table
some customer review
functionalitys of the app (in a nice way shown)
Section showing screens of a demo shop.
footer with ccdetails, socialmedia, newsletter

I have been playing abit myself with a theme, but no development/designer experience. And we really need a very professional and custom look.

Ps. we are an ecommerce company so if we find any good designer here, we will have enough work for you.

Some competitors in this field;

http://shrt.example/k7Tq2Zw
http://shrt.example/p3Nx9Ld

Here is a design we like
http://brelunoweb.example/

Hoping for some great concepts!

Kind Regards and good luck!

Some screenshots which can be used for app demo;

UPDATE BRIEF

We would like to add a section for features of the app.
We would like to show a zelphone screen and all the most important features of the app and when clicking every feature the screen would change or the feature intened would be high lighted in some way.

The features and any content and info abt that can be used from
https://www.tovexa.example/features.html/

We need an how it works section aswell in the design, also that can be used content from here
https://www.tovexa.example/how-it-works/

Tovexa is our partner, so there work way and features are same as ours. We just want it in a different 'look and feel/design)

Reason: Getting very few good design at the moment. Same designers seem to be responding whith 5 designs at a time of low quality.

Target Market(s)

quillora webshop

Industry/Entity Type

Business

Number of Pages Required

1 page

Font styles to use
Sans Serif

Colors
0355a3
3176b5
85acd3
85cae6
33a6d7
0392cd
f59195
33b8a4

Requirements
Must have
• a creative and custom look, not a copied theme vibe.
Nice to have
• it would be nice if the entire design has a nice flow goinf through the site. The customers experience should be on point.
Should not have
• boring static experience

```html
<!DOCTYPE html>
<html lang="nl">
<head>
<meta charset="utf-8">
<title>Vorbo – Quillora app</title>
<link rel="stylesheet" href="https://fonts.googleapis.com/css2?family=Comfortaa:wght@700&family=Open+Sans:ital,wght@0,400;0,600;0,700;1,400&display=swap">
<style>
:root{
  --blue-deep:#0355a3;
  --blue-mid:#3176b5;
  --blue-sky:#0392cd;
  --blue-bright:#33a6d7;
  --blue-soft:#85acd3;
  --orange:#f6a21e;
  --ink:#222;
  --text:#666;
  --line:#e3e3e3;
  --white:#fff;
  --grey-bg:#eef0f2;
  --dark:#2b2b2b;
}
*{box-sizing:border-box;margin:0;padding:0}
html,body{width:1200px;height:3930px;overflow:hidden}
body{font-family:"Open Sans",sans-serif;color:var(--text);background:var(--white);position:relative}
.display{font-family:"Comfortaa",sans-serif;font-weight:700}
.abs{position:absolute}
section{position:absolute;left:0;width:1200px;overflow:hidden}

/* hero */
.hero{top:0;height:642px}
.hero-photo{position:absolute;inset:0;background:linear-gradient(110deg,#3a3229 0%,#5b4a3a 40%,#8b7a68 62%,#6a5c4e 100%)}
.hero-photo::after{content:"";position:absolute;inset:0;background:linear-gradient(90deg,rgba(0,0,0,.45),rgba(0,0,0,.05) 70%)}
.brand{font-family:"Comfortaa",sans-serif;font-weight:700;letter-spacing:-1px}
.hero .brand{left:98px;top:32px;font-size:62px;color:var(--white)}
.nav{right:100px;top:48px;display:flex;align-items:center;gap:30px;font-size:14px;font-weight:600;color:var(--white)}
.nav .demo{border:2px solid var(--white);border-radius:22px;padding:8px 16px}
.hero-title{left:98px;top:230px;font-size:46px;line-height:58px;color:var(--white)}
.btn{display:inline-block;border-radius:30px;font-size:15px;font-weight:700;text-align:center}
.btn-ghost{left:98px;top:418px;width:164px;height:46px;line-height:42px;border:2px solid var(--white);color:var(--white)}
.btn-solid{left:286px;top:418px;width:156px;height:46px;line-height:46px;background:var(--white);color:var(--blue-deep)}
.dots{display:flex;gap:10px}
.dots span{width:14px;height:14px;border-radius:50%;border:2px solid var(--white)}
.hero .dots{left:98px;top:500px}
.hero .dots span:first-child{background:var(--blue-bright);border-color:var(--blue-bright)}

/* welcome */
.welcome{top:642px;height:642px}
.sec-title{width:1200px;text-align:center;font-size:40px;color:var(--ink)}
.welcome .sec-title{top:50px}
.divider{left:525px;width:150px;height:14px}
.lead{left:160px;width:880px;text-align:center;font-size:13px;line-height:22px}
.welcome .lead{top:130px}
.tablet{left:165px;top:225px;width:300px;height:380px;border-radius:14px;background:linear-gradient(160deg,#d8b89a,#7d6a5a 55%,#c7a98e)}
.features{left:578px;top:238px;width:420px}
.feature{display:flex;gap:22px;height:94px}
.feature .icon{flex:0 0 64px;height:64px;border-radius:50%;border:2px solid #cfcfcf;display:flex;align-items:center;justify-content:center}
.feature h3{font-size:19px;font-weight:400;color:var(--ink);margin:4px 0 4px}
.feature p{font-size:12px;line-height:18px}
.read-more{left:590px;top:560px;width:122px;height:34px;line-height:30px;border:2px solid var(--blue-mid);border-radius:6px;font-size:12px;font-weight:700;color:var(--blue-deep);text-align:center}

/* reviews */
.reviews{top:1284px;height:437px}
.reviews-photo{position:absolute;inset:0;background:linear-gradient(180deg,#1d8fd1,#2a9ad8 55%,#1a86c6)}
.reviews .sec-title{top:60px;color:var(--white);font-size:36px}
.review{top:150px;width:310px;color:var(--white)}
.review p{font-style:italic;font-size:13px;line-height:22px}
.review .who{display:flex;align-items:center;gap:18px;margin-top:26px}
.avatar{width:72px;height:72px;border-radius:50%;border:3px solid var(--white);background:linear-gradient(135deg,#e8c9a8,#a9876b)}
.who b{display:block;font-size:13px;font-weight:400}
.stars{color:var(--orange);font-size:12px;letter-spacing:2px}
.reviews .dots{left:562px;top:368px}
.reviews .dots span{background:var(--white);width:12px;height:12px}
.reviews .dots span:first-child{background:transparent}

/* plans */
.plans{top:1721px;height:611px}
.plans .sec-title{top:55px;font-size:36px}
.plan{top:185px;width:318px;height:350px;border:1px solid var(--line);background:var(--white)}
.plan-head{height:130px;background:var(--blue-deep);position:relative}
.plan-price{position:absolute;left:100px;top:-52px;width:118px;height:118px;border-radius:50%;background:var(--orange);border:6px solid var(--white);box-shadow:0 0 0 5px var(--blue-deep);color:var(--white);text-align:center;font-size:25px;font-weight:600;line-height:28px;padding-top:26px}
.plan-name{position:absolute;left:0;width:100%;top:88px;text-align:center;color:var(--white);font-size:22px}
.plan ul{list-style:none;font-size:12px;text-align:center}
.plan li{height:40px;line-height:40px;border-bottom:1px solid var(--line);margin:0 10px}
.plan .sub{display:block;margin:14px auto 0;width:124px;height:32px;line-height:28px;border:2px solid var(--blue-mid);border-radius:4px;color:var(--blue-deep);font-size:13px;text-align:center}

/* app */
.app{top:2332px;height:498px;background:linear-gradient(180deg,#e9ebee,#f5f6f7)}
.app-title{left:158px;top:130px;font-size:50px;color:var(--blue-deep)}
.app-sub{left:158px;top:194px;font-size:15px;color:var(--blue-mid)}
.app-copy{left:158px;top:222px;width:440px;font-size:12px;line-height:19px}
.store{top:336px;width:148px;height:46px;border-radius:7px;background:#111;border:1px solid #555}
.hand-phone{left:800px;top:60px;width:310px;height:400px;border-radius:30px;background:linear-gradient(160deg,#e6c3a4,#b58e70 50%,#d9b596)}

/* screens */
.screens{top:2830px;height:623px}
.screens .sec-title{top:55px;font-size:36px}
.shot{top:160px;width:140px;height:385px;border-radius:24px;background:linear-gradient(180deg,#f3f3f3,#dcdcdc);border:1px solid #ccc}

/* newsletter */
.news{top:3453px;height:347px}
.news-photo{position:absolute;inset:0;background:linear-gradient(120deg,#1f1f1f,#3a3a3a 50%,#262626)}
.news .brand{width:1200px;text-align:center;top:40px;font-size:64px;color:var(--white)}
.news h2{top:130px;width:1200px;text-align:center;font-size:34px;color:var(--white)}
.news p{top:182px;width:1200px;text-align:center;font-size:15px;color:#ddd}
.news-form{left:268px;top:230px;width:664px;height:52px;display:flex}
.news-form .field{flex:1;background:var(--white);display:flex;align-items:center;gap:14px;padding-left:16px;font-size:12px;color:#999}
.news-form .go{width:160px;background:var(--blue-bright);color:var(--white);font-weight:700;font-size:16px;text-align:center;line-height:52px}
.mail-tab{left:574px;top:3772px;width:52px;height:52px;border-radius:50%;background:#f0f0f0;display:flex;align-items:center;justify-content:center}

/* footer */
.footer{top:3830px;height:100px}
.footer .brand{left:96px;top:24px;font-size:34px;color:var(--blue-deep)}
.social{left:222px;top:36px;display:flex;gap:8px}
.social span{width:24px;height:24px;border-radius:50%;background:#cfcfcf}
.copy{width:1200px;text-align:center;top:44px;font-size:12px}
.pay{right:100px;top:34px;display:flex;gap:8px}
.pay span{width:38px;height:26px;border-radius:3px;background:#e4e4e4;border:1px solid #d2d2d2}
</style>
</head>
<body>

<section class="hero">
  <div class="hero-photo" role="img" aria-label="Photo of hands holding a smartphone showing a webshop app"></div>
  <div class="abs brand">vorbo</div>
  <nav class="abs nav"><span>HOME</span><span>FEATURES</span><span>REVIEWS</span><span>SCREENS</span><span>SUPPORT</span><span class="demo">REQUEST A DEMO</span></nav>
  <h1 class="abs hero-title display">Direct meer<br>omzet met een<br>Quillora app</h1>
  <span class="abs btn btn-ghost">TELL ME MORE</span>
  <span class="abs btn btn-solid">SIGN ME UP</span>
  <div class="abs dots"><span></span><span></span><span></span></div>
</section>

<section class="welcome">
  <h2 class="abs sec-title display">welcome to vorbo</h2>
  <svg class="abs divider" style="top:108px" viewBox="0 0 150 14"><line x1="0" y1="7" x2="66" y2="7" stroke="#999"/><rect x="70" y="2" width="10" height="10" transform="rotate(45 75 7)" fill="none" stroke="#999"/><line x1="84" y1="7" x2="150" y2="7" stroke="#999"/></svg>
  <p class="abs lead">Sed ut perspiciatis unde omnis iste natus error sit voluptatem accusantium doloremque laudantium, totam rem aperiam, eaque ipsa quae ab illo inventore veritatis et quasi architecto beatae vitae dicta sunt explicabo. Nemo enim ipsam voluptatem quia voluptas sit aspernatur aut odit aut fugit, sed quia consequuntur magni dolores eos qui ratione voluptatem sequi nesciunt. Neque porro quisquam est, qui dolorem ipsum quia dolor sit amet, consectetur.</p>
  <div class="abs tablet" role="img" aria-label="Hands holding a tablet showing the demo shop app"></div>
  <div class="abs features">
    <div class="feature">
      <div class="icon"><svg width="30" height="26" viewBox="0 0 30 26"><path d="M15 2C8 2 2 6 2 11c0 3 2 5 4 6l-1 6 6-4c1 0 3 .5 4 .5 7 0 13-4 13-9S22 2 15 2z" fill="#555"/></svg></div>
      <div><h3>Live Chat Messages</h3><p>Lorem ipsum dolor sit amet, consectetur adipiscing elit, sed do eiusmod tempor incididunt ut labore et dolore magna</p></div>
    </div>
    <div class="feature">
      <div class="icon"><svg width="30" height="22" viewBox="0 0 30 22"><rect x="1" y="1" width="28" height="20" fill="none" stroke="#555" stroke-width="2"/><path d="M1 1l14 11L29 1" fill="none" stroke="#555" stroke-width="2"/></svg></div>
      <div><h3>Messages Inbox</h3><p>Lorem ipsum dolor sit amet, consectetur adipiscing elit, sed do eiusmod tempor incididunt ut labore et dolore magna</p></div>
    </div>
    <div class="feature">
      <div class="icon"><svg width="28" height="28" viewBox="0 0 28 28"><rect x="2" y="4" width="24" height="22" fill="none" stroke="#555" stroke-width="2"/><line x1="2" y1="10" x2="26" y2="10" stroke="#555" stroke-width="2"/><line x1="8" y1="1" x2="8" y2="7" stroke="#555" stroke-width="2"/><line x1="20" y1="1" x2="20" y2="7" stroke="#555" stroke-width="2"/><g fill="#555"><rect x="6" y="13" width="3" height="3"/><rect x="12" y="13" width="3" height="3"/><rect x="18" y="13" width="3" height="3"/><rect x="6" y="19" width="3" height="3"/><rect x="12" y="19" width="3" height="3"/></g></svg></div>
      <div><h3>Calendar / Planner</h3><p>Lorem ipsum dolor sit amet, consectetur adipiscing elit, sed do eiusmod tempor incididunt ut labore et dolore magna</p></div>
    </div>
  </div>
  <span class="abs read-more">READ MORE ➔</span>
</section>

<section class="reviews">
  <div class="reviews-photo" role="img" aria-label="Blue tinted city skyline"></div>
  <h2 class="abs sec-title display">customer review</h2>
  <div class="abs review" style="left:100px"><p>“ Lorem ipsum dolor sit amet, consectetur adipiscing elit, sed do eiusmod tempor incididunt ut labore et dolore magna aliqua Unde omnis, consequuntur.</p><div class="who"><div class="avatar" role="img" aria-label="Customer portrait"></div><div><b>JOHN DOE</b><span class="stars">★★★★★</span></div></div></div>
  <div class="abs review" style="left:455px"><p>“ Lorem ipsum dolor sit amet, consectetur adipiscing elit, sed do eiusmod tempor incididunt ut labore et dolore magna aliqua Unde omnis, consequuntur.</p><div class="who"><div class="avatar" role="img" aria-label="Customer portrait"></div><div><b>JOHN DOE</b><span class="stars">★★★★★</span></div></div></div>
  <div class="abs review" style="left:815px"><p>“ Lorem ipsum dolor sit amet, consectetur adipiscing elit, sed do eiusmod tempor incididunt ut labore et dolore magna aliqua Unde omnis, consequuntur.</p><div class="who"><div class="avatar" role="img" aria-label="Customer portrait"></div><div><b>JOHN DOE</b><span class="stars">★★★★★</span></div></div></div>
  <div class="abs dots"><span></span><span></span><span></span><span></span></div>
</section>

<section class="plans">
  <h2 class="abs sec-title display">choose the plan</h2>
  <div class="abs plan" style="left:100px"><div class="plan-head"><div class="plan-price">$25.00<br>Month</div><div class="plan-name display">professional</div></div><ul><li>Sed ut perspiciatis unde omnis</li><li>Nemo enim ipsam voluptatem</li><li>Ut enim ad minima veniam</li><li>Lorem ipsum dolor</li></ul><span class="sub">Subscription</span></div>
  <div class="abs plan" style="left:441px"><div class="plan-head"><div class="plan-price">$25.00<br>Month</div><div class="plan-name display">premium</div></div><ul><li>Sed ut perspiciatis unde omnis</li><li>Nemo enim ipsam voluptatem</li><li>Ut enim ad minima veniam</li><li>Lorem ipsum dolor</li></ul><span class="sub">Subscription</span></div>
  <div class="abs plan" style="left:782px"><div class="plan-head"><div class="plan-price">$25.00<br>Month</div><div class="plan-name display">ultimate</div></div><ul><li>Sed ut perspiciatis unde omnis</li><li>Nemo enim ipsam voluptatem</li><li>Ut enim ad minima veniam</li><li>Lorem ipsum dolor</li></ul><span class="sub">Subscription</span></div>
</section>

<section class="app">
  <h2 class="abs app-title display">The app</h2>
  <p class="abs app-sub">Choose your native platform and get started!</p>
  <p class="abs app-copy">Sed ut perspiciatis unde omnis iste natus error sit voluptatem accusantium doloremque laudantium, totam rem aperiam, eaque ipsa quae ab illo inventore veritatis et quasi architecto beatae vitae dicta sunt explicabo. Nemo enim ipsam voluptatem quia voluptas sit aspernatur aut odit aut fugit, sed quia.</p>
  <div class="abs store" style="left:158px" role="img" aria-label="First mobile platform download button"></div>
  <div class="abs store" style="left:322px" role="img" aria-label="Second mobile platform download button"></div>
  <div class="abs hand-phone" role="img" aria-label="Hand holding a smartphone with the shop checkout screen"></div>
</section>

<section class="screens">
  <h2 class="abs sec-title display">vorbo screens</h2>
  <div class="abs shot" style="left:185px" role="img" aria-label="Phone showing the demo shop home screen"></div>
  <div class="abs shot" style="left:400px" role="img" aria-label="Phone showing the demo shop product list"></div>
  <div class="abs shot" style="left:615px" role="img" aria-label="Phone showing the demo shop product grid"></div>
  <div class="abs shot" style="left:830px" role="img" aria-label="Phone showing a demo shop product detail"></div>
</section>

<section class="news">
  <div class="news-photo" role="img" aria-label="Dark photo of a person using a phone"></div>
  <div class="abs brand">vorbo</div>
  <h2 class="abs display">Get Notified of any Updates!</h2>
  <p class="abs">Subscribe to our newsletter to be notified about new version release</p>
  <div class="abs news-form"><div class="field"><svg width="18" height="14" viewBox="0 0 18 14"><rect x="1" y="1" width="16" height="12" fill="none" stroke="#bbb"/><path d="M1 1l8 7 8-7" fill="none" stroke="#bbb"/></svg>Enter Your E-mail Adress</div><div class="go">SIGN UP</div></div>
</section>

<div class="abs mail-tab"><svg width="20" height="15" viewBox="0 0 20 15"><rect x="1" y="1" width="18" height="13" fill="none" stroke="#555" stroke-width="1.5"/><path d="M1 1l9 7 9-7" fill="none" stroke="#555" stroke-width="1.5"/></svg></div>

<footer class="abs footer" style="left:0;width:1200px">
  <div class="abs brand">vorbo</div>
  <div class="abs social"><span></span><span></span><span></span></div>
  <div class="abs copy">Copyright © Vorbo app 2016, All rights reserved</div>
  <div class="abs pay"><span></span><span></span><span></span><span></span><span></span></div>
</footer>

</body>
</html>
```